Custom Cabinet Shop Needs a website design

Hi,
We need a website for a Custom Cabinet Shop and Cabinet parts manufacturing business.
The business has two sides to it. One side provides custom Kitchens, vanities, entertainment units, offices and what not to homeowners and contractors.
The 2nd side of the business provides built to order cabinet boxes and other parts required to put together a project to other cabinet shops, small contractors looking to install there own cabinets.
Website will need a Gallery to display work.
Color scheme to go well with logo.
current website is www.brambleoakcustomcabinets.com
being changed to www.brambleoak.ca
Logo Included in attached files.
Tagline "Joinery with Spirit"
Mission Statement "Our passion is to deliver inspired cabinetry solutions to suit all your needs, supported by our phenomenal star class customer service"
The website should convey quality and professionalism.
Thank you.
Homeowners/ Contractors
Entertainment

```html
<!DOCTYPE html>
<html lang="en">
<head>
<meta charset="utf-8">
<title>Brambleoak Custom Cabinets</title>
<link href="https://fonts.googleapis.com/css2?family=Open+Sans:wght@400;600;700&family=Tinos&family=Kaushan+Script&display=swap" rel="stylesheet">
<style>
:root{
  --orange:#f15a22;
  --orange-light:#f7875a;
  --black:#000;
  --footer:#2a2a2a;
  --light:#f1f1f1;
  --text:#111;
  --white:#fff;
}
*{margin:0;padding:0;box-sizing:border-box}
html,body{width:950px;height:1200px;overflow:hidden}
body{font-family:'Open Sans',sans-serif;background:var(--white);position:relative}
.topline{position:absolute;top:0;left:0;width:950px;height:4px;background:var(--orange)}
.header{position:absolute;top:4px;left:0;width:950px;height:81px;background:var(--black)}
.brand{position:absolute;left:52px;top:27px;display:flex;align-items:center;gap:10px;color:var(--white);font-weight:700;font-size:21px;letter-spacing:1px}
.brand-mark{width:22px;height:22px;background:var(--orange)}
.nav{position:absolute;top:27px;left:505px;display:flex;align-items:center;font-size:11px;font-weight:600;color:var(--white)}
.nav a{color:inherit;text-decoration:none;padding:0 20px;line-height:29px}
.nav a.active{background:var(--orange);padding:0 14px;margin-right:6px}
.hero{position:absolute;top:85px;left:0;width:950px;height:372px;
  background:
    radial-gradient(ellipse 260px 140px at 420px 210px,rgba(214,150,86,.75),rgba(214,150,86,0) 70%),
    radial-gradient(ellipse 120px 120px at 330px 150px,rgba(230,190,130,.45),rgba(230,190,130,0) 70%),
    linear-gradient(180deg,rgba(0,0,0,0) 62%,rgba(96,62,34,.85) 100%),
    linear-gradient(90deg,#15171b 0%,#23262b 18%,#4a3a2c 32%,#6e5138 48%,#5c4838 62%,#7d7063 75%,#8f8577 100%)}
.caption{position:absolute;left:45px;top:263px;width:255px;height:50px;background:rgba(20,20,20,.6);color:var(--white);font-family:'Kaushan Script',cursive;font-size:21px;padding:11px 0 0 43px}
.arrow{position:absolute;top:168px;width:34px;height:34px}
.arrow.prev{left:5px}.arrow.next{left:909px}
.welcome{position:absolute;top:457px;left:0;width:950px;height:178px;background:var(--light);text-align:center;font-family:'Tinos',serif}
.welcome h1{font-weight:400;color:var(--orange);font-size:27px;margin-top:22px}
.welcome p{font-size:18px;color:var(--text);line-height:36px;margin-top:12px}
.works{position:absolute;top:635px;left:0;width:950px;height:450px;background:var(--orange)}
.works h2{font-family:'Tinos',serif;font-weight:400;color:var(--white);font-size:22px;text-align:center;margin-top:14px}
.grid{position:absolute;left:97px;top:58px;display:grid;grid-template-columns:repeat(4,171px);column-gap:24px;row-gap:24px}
.thumb{width:171px;height:171px;border:3px solid var(--orange-light)}
.footer{position:absolute;top:1085px;left:0;width:950px;height:115px;background:var(--footer);color:var(--white);text-align:center;font-size:11px}
.contact{position:absolute;top:28px;left:304px;display:flex;align-items:center;font-weight:600}
.contact .item{display:flex;align-items:center}
.contact .item svg{margin-right:13px}
.contact .item + .item{margin-left:32px}
.contact em{font-style:normal;color:var(--orange);font-weight:400;margin-left:3px}
.links{position:absolute;top:56px;left:0;width:950px}
.copy{position:absolute;top:78px;left:0;width:950px}
</style>
</head>
<body>
<div class="topline"></div>
<header class="header">
  <div class="brand"><span class="brand-mark"></span>BRAMBLEOAK</div>
  <nav class="nav">
    <a class="active">HOME</a><a>GALLERY</a><a>SERVICES</a><a>WARRANTY</a><a>CONTACT</a>
  </nav>
</header>
<section class="hero" role="img" aria-label="Basement bar with live-edge wood counter, stone base, bar stools, pendant lights and wine rack">
  <div class="caption">Joinery with Spirit</div>
  <svg class="arrow prev" viewBox="0 0 34 34"><circle cx="17" cy="17" r="16" fill="none" stroke="#fff" stroke-width="1.5"/><path d="M19 12l-5 5 5 5" fill="none" stroke="#fff" stroke-width="2"/></svg>
  <svg class="arrow next" viewBox="0 0 34 34"><circle cx="17" cy="17" r="16" fill="none" stroke="#fff" stroke-width="1.5"/><path d="M15 12l5 5-5 5" fill="none" stroke="#fff" stroke-width="2"/></svg>
</section>
<section class="welcome">
  <h1>Welcome</h1>
  <p>" Our passion is to deliver inspired cabinetry solutions to suit all your needs, supported by<br>our phenomenal star class customer service "</p>
</section>
<section class="works">
  <h2>Our Works</h2>
  <div class="grid">
    <div class="thumb" role="img" aria-label="Dining nook with wood table and window bench" style="background:linear-gradient(180deg,#e8eef2 0%,#b9c3c4 35%,#a07a5a 65%,#5e4634 100%)"></div>
    <div class="thumb" role="img" aria-label="White kitchen with granite island" style="background:linear-gradient(180deg,#efece6 0%,#c9c2b8 40%,#6d6158 70%,#2e2926 100%)"></div>
    <div class="thumb" role="img" aria-label="Dark wet bar cabinetry" style="background:linear-gradient(180deg,#7c7b72 0%,#4a4842 45%,#1d1b19 75%,#262320 100%)"></div>
    <div class="thumb" role="img" aria-label="White kitchen with dark wood island" style="background:linear-gradient(180deg,#f2efe9 0%,#dcd6cc 40%,#6a4c38 65%,#c9a57c 100%)"></div>
    <div class="thumb" role="img" aria-label="Built-in white shelving units" style="background:linear-gradient(180deg,#4f5b63 0%,#c9d2d8 25%,#dde3e6 70%,#8b8e7c 100%)"></div>
    <div class="thumb" role="img" aria-label="Kitchen island with pendant light" style="background:linear-gradient(180deg,#f1ede6 0%,#d7c9bb 40%,#8d5b3f 55%,#d9d5cf 72%,#1f1c1a 100%)"></div>
    <div class="thumb" role="img" aria-label="Dark entertainment wall unit" style="background:linear-gradient(180deg,#e5e3df 0%,#b9b5ae 22%,#2e2521 40%,#2a221e 85%,#d6d3ce 100%)"></div>
    <div class="thumb" role="img" aria-label="Cherry media cabinet with television" style="background:linear-gradient(180deg,#6a6461 0%,#2a2828 45%,#6a2e1c 60%,#4a1f14 100%)"></div>
  </div>
</section>
<footer class="footer">
  <div class="contact">
    <span class="item"><svg width="14" height="14" viewBox="0 0 24 24"><path fill="#fff" d="M6.6 10.8a15 15 0 006.6 6.6l2.2-2.2a1 1 0 011-.25 11.4 11.4 0 003.6.6 1 1 0 011 1V20a1 1 0 01-1 1A17 17 0 013 4a1 1 0 011-1h3.5a1 1 0 011 1 11.4 11.4 0 00.6 3.6 1 1 0 01-.25 1z"/></svg>CALL US :<em>+2245550193</em></span>
    <span class="item"><svg width="14" height="11" viewBox="0 0 14 11"><rect width="14" height="11" fill="#fff"/><path d="M0 0l7 6 7-6" fill="none" stroke="#2a2a2a" stroke-width="1.3"/></svg>EMAIL US :<em>info@brambleoak.ca</em></span>
  </div>
  <div class="links">Home &nbsp;|&nbsp; Gallery &nbsp;|&nbsp; Services &nbsp;|&nbsp; Warranty &nbsp;|&nbsp; Contact</div>
  <div class="copy">© 2015 brambleoakcustomcabinets.</div>
</footer>
</body>
</html>
```